Design website home page for pathology consulting company

Starting a new consulting company with anatomic pathologists focused on expert diagnosis and second opinions on difficult pathology cases. In the near future we will be incorporating next generation diagnostics for rare diseases of childhood into the business. These include discovery and testing of DNA for mutations.

The company is formed around one of the best known pathologists in the world named Marcel "Biscuit" Trowell. The name of the company is "BiscuitLab"

We had a logo design by SketchForum - it is great. I will attach file as soon as I have it (contest ending today). Our company is medical, uses microscopes, DNA, probably will focus on childhood diseases but not solely on childhood diseases. we're not particularly conservative, but the customers we want to appeal to include older practicing pathologists as well as patients (sometimes parents) looking for second opinions.

Think a group of expert doctors diagnosing disease through the microscope and through DNA technology, ages ranging from 35-75 all trained by the best pathologist in the world - "Biscuit"

We receive glass slides from diseases from patients all over the world from docs who need an expert to tell them what is the diagnosis. So "path to the diagnosis" is also part of the company marketing message.

We want the website design to describe our company but be very simple to find what one is looking for as we will use it as the launch page to:
1) order services
2) check results/reports
3) set up new account
4) speak with one of the pathologists
5) see our test menu
6) access our educational material/webinars
Updates

Update - looking for home page design and then finalists will ask for second page design to keep with theme - ok?

Reason: realized this project isn't web design but web home page design - thanks

Reason: Holidays for some in next two weeks

Reason: Hot discussion among collaborators for a few of the submissions. Will provide detail individually this weekend. Thanks so much for all the submissions!

Target Market(s)

Referring pathologists, physicians who want second opinions on pathology disease diagnosis, patients who have had biopsies (either patients themselves or parents of patients), generally high education level

Industry/Entity Type

Marketing

Requirements
Must have
• BiscuitLab
Next Generation Pathology Consultants

```html
<!DOCTYPE html>
<html lang="en">
<head>
<meta charset="utf-8">
<title>BiscuitLab — Next Generation Pathology Consultants</title>
<link href="https://fonts.googleapis.com/css2?family=Cinzel:wght@400;600&family=Arimo:wght@400;700&display=swap" rel="stylesheet">
<style>
:root{
  --blue:#1a4f8f;
  --blue-dark:#123c70;
  --ink:#2a2a2a;
  --grey:#6d6d6d;
  --line:#d6d6d6;
  --footer:#555;
  --white:#fff;
}
*{box-sizing:border-box;margin:0;padding:0}
html,body{width:1200px;height:1013px;overflow:hidden;background:var(--white);font-family:"Arimo",Arial,sans-serif;color:var(--ink)}
.page{position:relative;width:1200px;height:1013px}

/* header */
.brand{position:absolute;left:200px;top:14px;width:150px}
.brand-mark{display:block;width:64px;height:64px;border-radius:50%;background:var(--blue);margin:0 0 4px 38px}
.brand-name{font-family:"Cinzel",Georgia,serif;font-weight:600;font-size:22px;color:var(--blue);line-height:22px;white-space:nowrap}
.brand-tag{font-size:7.5px;color:var(--grey);margin-top:2px;white-space:nowrap}

.account{position:absolute;top:29px;left:804px;display:flex;gap:7px}
.btn{font-family:"Cinzel",Georgia,serif;font-weight:600;color:var(--white);font-size:13px;height:30px;line-height:30px;border-radius:2px;text-align:center;white-space:nowrap}
.btn-login{background:linear-gradient(#a0a0a0,#7a7a7a);width:72px}
.btn-new{background:linear-gradient(#2a65a8,var(--blue-dark));width:117px}

.search{position:absolute;left:752px;top:76px;width:248px;height:31px;border:1px solid var(--line);font-family:"Cinzel",Georgia,serif;font-size:13px;color:#777;padding:7px 10px}
.search svg{position:absolute;right:7px;top:7px}

.rule{position:absolute;left:0;top:123px;width:1200px;border-top:1px dashed var(--line)}
.nav{position:absolute;left:200px;top:134px;display:flex;font-family:"Cinzel",Georgia,serif;font-size:14px;color:#555;white-space:nowrap}
.nav a{padding:0 8px;margin-right:4px;height:31px;color:inherit;text-decoration:none}
.nav a.current{color:var(--blue);font-weight:600;border-bottom:3px solid var(--blue)}
.social{position:absolute;left:912px;top:130px;display:flex;gap:4px}
.social span{width:27px;height:27px;border-radius:50%}

/* hero */
.hero{position:absolute;left:0;top:165px;width:1200px;height:584px;background:linear-gradient(100deg,#d8d2cd 0%,#e9e4df 35%,#c9b2a0 55%,#e6e6ea 75%,#cfcfd4 100%)}
.arrow{position:absolute;top:280px}
.headline{font-family:"Cinzel",Georgia,serif;line-height:1;white-space:nowrap}
.headline span{position:absolute;left:200px}
.headline .l1{top:449px;font-size:45px;color:#1c1c1c}
.headline .l2{top:494px;font-size:46px;color:var(--blue)}
.headline .l3{top:545px;font-size:19.5px;color:#333}
.hero-btn{position:absolute;top:525px;height:39px;line-height:39px;font-family:"Cinzel",Georgia,serif;font-weight:600;font-size:20px;color:var(--white);text-align:center;border-radius:2px;white-space:nowrap}
.hero-btn.more{left:536px;width:154px;background:linear-gradient(#2b68ab,var(--blue-dark))}
.hero-btn.join{left:700px;width:116px;background:linear-gradient(#555,#2e2e2e)}

/* features */
.feature{position:absolute;top:786px;width:180px}
.feature h2{font-family:"Cinzel",Georgia,serif;font-weight:400;font-size:20px;color:var(--blue);line-height:1;margin-bottom:8px;white-space:nowrap}
.feature p{font-size:9.6px;line-height:11.6px;color:#444}
.feature .link{position:absolute;top:124px;font-size:10.5px;font-weight:700;color:var(--blue);white-space:nowrap}
.divider{position:absolute;top:789px;height:134px;border-left:1px solid #e4e4e4}
.video{width:183px;height:85px;background:linear-gradient(90deg,#9aa4ac,#c8c6c2 55%,#6c7580);position:relative}
.video .play{position:absolute;left:71px;top:26px}
.talk{position:absolute;left:818px;top:789px;width:182px;height:125px;background:linear-gradient(90deg,#7f8c96,#b9c4cc 60%,#dfe5ea)}
.talk .t1{position:absolute;left:8px;top:18px;font-family:"Cinzel",Georgia,serif;font-size:20px;color:var(--white);white-space:nowrap}
.talk .t2{position:absolute;left:8px;top:56px;font-family:"Cinzel",Georgia,serif;font-size:9px;color:var(--white);line-height:1.2;white-space:nowrap}
.talk .t2 b{font-size:13px;font-weight:400}
.talk .go{position:absolute;left:9px;top:94px;width:89px;height:19px;line-height:19px;text-align:center;font-family:"Cinzel",Georgia,serif;font-size:12px;color:var(--white);background:var(--blue);white-space:nowrap}

/* footer */
.footer{position:absolute;left:0;top:957px;width:1200px;height:56px;background:linear-gradient(#5e5e5e,var(--footer));font-size:10px;color:#eee}
.footer nav{position:absolute;left:202px;top:22px;display:flex;gap:22px}
.footer .copy{position:absolute;right:201px;top:22px;color:#aaa}
</style>
</head>
<body>
<div class="page">
  <header>
    <div class="brand">
      <span class="brand-mark"></span>
      <div class="brand-name">BiscuitLab</div>
      <div class="brand-tag">Next Generation Pathology Consultants</div>
    </div>
    <div class="account">
      <span class="btn btn-login">Login</span>
      <span class="btn btn-new">New Account</span>
    </div>
    <div class="search">SEARCH
      <svg width="16" height="16" viewBox="0 0 16 16"><circle cx="6.5" cy="6.5" r="5" fill="none" stroke="#1a4f8f" stroke-width="2.4"/><line x1="10" y1="10" x2="14.5" y2="14.5" stroke="#1a4f8f" stroke-width="2.6" stroke-linecap="round"/></svg>
    </div>
    <div class="rule"></div>
    <nav class="nav">
      <a class="current">HOME</a><a>ABOUT US</a><a>SERVICES</a><a>EDUCATIONAL MATERIAL</a><a>TEST MENU</a><a>CONTACT US</a>
    </nav>
    <div class="social">
      <span style="background:#2c5aa0" aria-label="Social profile"></span>
      <span style="background:#27a9e1" aria-label="Social profile"></span>
      <span style="background:#1e6ea7" aria-label="Social profile"></span>
    </div>
  </header>

  <section class="hero" role="img" aria-label="Photo of a doctor with a stethoscope comforting a young girl">
    <svg class="arrow" style="left:38px" width="20" height="30" viewBox="0 0 20 30"><polyline points="15,4 5,15 15,26" fill="none" stroke="#fff" stroke-width="5"/></svg>
    <svg class="arrow" style="left:1142px" width="20" height="30" viewBox="0 0 20 30"><polyline points="5,4 15,15 5,26" fill="none" stroke="#fff" stroke-width="5"/></svg>
    <div class="headline">
      <span class="l1">Next Generation</span>
      <span class="l2">Diagnostics</span>
      <span class="l3">For Rare Diseases of Children</span>
    </div>
    <span class="hero-btn more">Learn More</span>
    <span class="hero-btn join">Join Us</span>
  </section>

  <section>
    <div class="feature" style="left:202px">
      <h2>Services</h2>
      <p>Lorem ipsum dolor sit amet, sed diam consectetuer adipiscing elit, sed diam nonummy nibh euismod tincidunt ut laoreet dolore magna aliquam erat volutpat. Ut wisi enim ad minim veniam, quis nostrud exerci tation. Ut wisi enim ad minim veniam, quis nostrud.</p>
      <span class="link">Learn More</span>
    </div>
    <div class="divider" style="left:391px"></div>
    <div class="feature" style="left:404px;width:182px">
      <h2>Results / Reports</h2>
      <p>Ut wisi enim ad minim veniam, quis nostrud exerci tation ullamcorper suscipit lobortis nisl ut aliquip ex ea commodo consequat. Duis autem vel eum iriure dolor in hendrerit in vulputate velit esse molestie. Ut wisi enim ad minim veniam, quis nostrud exerci tation.</p>
      <span class="link">See your Results/Reports</span>
    </div>
    <div class="divider" style="left:595px"></div>
    <div class="feature" style="left:608px;width:183px">
      <h2>Recent Webinars</h2>
      <div class="video" role="img" aria-label="Webinar still of a doctor with a young boy">
        <svg class="play" width="34" height="34" viewBox="0 0 34 34"><circle cx="17" cy="17" r="15" fill="#fff" stroke="#333" stroke-width="2"/><polygon points="13,9 25,17 13,25" fill="#333"/></svg>
      </div>
      <span class="link">View All Webinars</span>
    </div>
    <div class="divider" style="left:804px"></div>
    <div class="talk" role="img" aria-label="Photo of a smiling pathologist in a lab coat">
      <span class="t1">Talk To Us</span>
      <span class="t2">Talk to one of our<br><b>Pathologists</b></span>
      <span class="go">Click Here</span>
    </div>
  </section>

  <footer class="footer">
    <nav><span>Home</span><span>About Us</span><span>Contact Us</span><span>Privacy Policy</span><span>Terms of Use</span></nav>
    <span class="copy">Copyright © 2013 BiscuitLab.com. All rights reserved.</span>
  </footer>
</div>
</body>
</html>
```